KRV Photography Business Card Design

I would like a business card designed in the shape of a camera.
Would like to see various camera designs. Would like to see what the card looks like in different colors. Would like to see which logo looks better on the various camera designs so please show me some with the white logo and some with the black logo. If you need a different file formats please let me know.
Project Deadline Extended Reason: My grandfather passed away and dealing with funeral plans so need to extend deadline. Added Tuesday, March 1, 2016
Project Deadline Extended
Reason: I just got back from out of town. My grandfather's passing was the primary focus for me these past few weeks and the funeral is over so now I will concentrate on picking my business card design. I really appreciate each designer who has taken the time to submit a design. Your effort has not gone unnoticed. I look forward to seeing more amazing designs.
Business
Contact Information for Business Card
Dorine
555-418-2706
https://www.facebook.com/krvphotographyfreelance/
MonaDorine@krv-photography.example

```html
<!DOCTYPE html>
<html lang="en">
<head>
<meta charset="utf-8">
<title>KRV Photography – Business Card</title>
<link rel="stylesheet" href="https://fonts.googleapis.com/css2?family=Cinzel:wght@400;500&family=Open+Sans:wght@400;700&display=swap">
<style>
  :root {
    --stage: #000000;
    --paper: #f3f3f3;
    --gold: #c99a3c;
    --gold-light: #f0cf7e;
    --gold-deep: #b9842c;
    --ink: #333333;
    --white: #ffffff;
  }
  * { margin: 0; padding: 0; box-sizing: border-box; }
  html, body { width: 1200px; height: 900px; overflow: hidden; background: var(--stage); }
  .canvas { position: relative; width: 1200px; height: 900px; }

  .card { position: absolute; top: 200px; width: 310px; height: 502px; overflow: hidden; }

  .card-front {
    left: 265px;
    background: var(--paper);
    border-radius: 70px 0 70px 0;
  }
  .brand-circle {
    position: absolute; left: 113px; top: 30px;
    width: 84px; height: 84px; border-radius: 50%;
    background: linear-gradient(135deg, var(--gold-light), var(--gold-deep));
  }
  .brand-name {
    position: absolute; left: 0; right: 0; top: 128px;
    text-align: center;
    font-family: "Cinzel", serif; font-weight: 500;
    font-size: 23px; color: var(--gold); letter-spacing: 0.5px;
  }
  .contact { position: absolute; left: 27px; top: 326px; font-family: "Open Sans", sans-serif; color: var(--ink); }
  .contact-name { font-weight: 700; font-size: 17px; color: var(--gold); letter-spacing: 0.3px; }
  .contact-title { font-size: 14px; margin-top: 2px; }
  .contact-address { font-size: 13px; line-height: 16px; margin-top: 18px; }
  .contact-lines { list-style: none; margin-top: 12px; font-size: 13px; line-height: 19px; }
  .contact-lines li { display: flex; align-items: center; gap: 6px; }
  .contact-lines svg { width: 10px; height: 9px; fill: var(--gold); }

  .card-back {
    left: 641px;
    border-radius: 0 70px 0 70px;
  }
  .back-pattern {
    position: absolute; inset: 0;
    background: radial-gradient(circle at 50% 48%, #f3d27f 0%, #dcaa4e 45%, var(--gold-deep) 100%);
  }
  .back-mark {
    position: absolute; left: 65px; top: 150px;
    width: 180px; height: 180px; border-radius: 50%;
    background: var(--white);
    display: flex; align-items: center; justify-content: center; text-align: center;
    font-family: "Cinzel", serif; font-weight: 500;
    font-size: 22px; line-height: 28px; color: var(--gold);
  }
</style>
</head>
<body>
<main class="canvas">
  <section class="card card-front">
    <div class="brand-circle"></div>
    <div class="brand-name">KRV Photography</div>
    <div class="contact">
      <div class="contact-name">MONA DORINE</div>
      <div class="contact-title">Managing Director</div>
      <div class="contact-address">1234, Address Goes Here<br>Country Name, 123456</div>
      <ul class="contact-lines">
        <li><svg viewBox="0 0 10 9"><path d="M0 3 Q5 -1 10 3 L8 4 L7 3 L3 3 L2 4 Z M2 5 H8 L9 9 H1 Z"/></svg>555-418-2706</li>
        <li><svg viewBox="0 0 10 9"><rect x="0" y="1" width="10" height="7"/></svg>MonaDorine@krv-photography.example</li>
      </ul>
    </div>
  </section>

  <section class="card card-back">
    <div class="back-pattern" role="img" aria-label="Gold background with a faint repeating brand monogram pattern"></div>
    <div class="back-mark">KRV<br>Photography</div>
  </section>
</main>
</body>
</html>
```